Vantiqo custom business card design

Need a authentic, innovative business card design for a new mobile app business. I am uploading a few screen images from our app for you to view. I would like app design theme to match business card design. I can also send logo images.

```html
<!DOCTYPE html>
<html lang="en">
<head>
<meta charset="utf-8">
<title>Vantiqo Business Card</title>
<link href="https://fonts.googleapis.com/css2?family=Raleway:wght@400;500;800&display=swap" rel="stylesheet">
<style>
  :root {
    --page-bg: #d9d9d9;
    --card-light: #ededed;
    --card-lavender: #e4dde8;
    --brand-purple: #5f0f8f;
    --text-dark: #2b2b2b;
    --text-muted: #6a6a6a;
    --card-black: #030303;
    --card-grey: #5a5a5a;
    --white: #ffffff;
  }
  * { margin: 0; padding: 0; box-sizing: border-box; }
  html, body { width: 1200px; height: 1079px; overflow: hidden; }
  body {
    background: var(--page-bg);
    font-family: "Raleway", sans-serif;
    display: flex;
    align-items: center;
    justify-content: center;
    gap: 80px;
  }
  .card {
    width: 440px;
    height: 700px;
    border-radius: 28px;
    overflow: hidden;
    position: relative;
    box-shadow: 0 10px 30px rgba(0,0,0,0.18);
  }
  .card-front {
    background: linear-gradient(180deg, var(--card-light) 0%, var(--card-light) 55%, var(--card-lavender) 100%);
    display: flex;
    flex-direction: column;
    align-items: center;
    padding-top: 108px;
  }
  .icon-badge {
    width: 34px; height: 34px;
    border-radius: 50%;
    background: var(--brand-purple);
    display: flex; align-items: center; justify-content: center;
  }
  .icon-badge svg { width: 20px; height: 20px; fill: var(--white); }
  .person-name {
    margin-top: 22px;
    font-size: 40px;
    font-weight: 400;
    color: var(--brand-purple);
    line-height: 1.1;
  }
  .person-title {
    font-size: 26px;
    font-weight: 500;
    color: var(--text-dark);
    margin-top: 4px;
  }
  .contact-icons {
    display: flex;
    gap: 14px;
    margin-top: 44px;
  }
  .contact-list {
    list-style: none;
    text-align: center;
    margin-top: 26px;
  }
  .contact-list li {
    font-size: 24px;
    color: var(--text-muted);
    line-height: 40px;
  }
  .card-back {
    background: linear-gradient(160deg, var(--card-black) 0%, var(--card-black) 58%, var(--card-grey) 100%);
    display: flex;
    flex-direction: column;
    align-items: center;
    justify-content: center;
    padding-bottom: 40px;
  }
  .brand-dot {
    width: 150px; height: 150px;
    border-radius: 50%;
    background: var(--brand-purple);
  }
  .brand-name {
    margin-top: 28px;
    font-size: 56px;
    font-weight: 800;
    color: var(--white);
  }
</style>
</head>
<body>
  <section class="card card-front">
    <div class="icon-badge" aria-hidden="true">
      <svg viewBox="0 0 20 20"><circle cx="10" cy="7" r="4"/><path d="M3 17c0-4 3-6 7-6s7 2 7 6z"/></svg>
    </div>
    <h1 class="person-name">Elena Marsh</h1>
    <p class="person-title">CEO/Founder</p>
    <div class="contact-icons" aria-hidden="true">
      <div class="icon-badge">
        <svg viewBox="0 0 20 20"><path d="M5 3l3 3-2 2c1 2 3 4 5 5l2-2 3 3-2 3C8 16 4 12 3 5z"/></svg>
      </div>
      <div class="icon-badge">
        <svg viewBox="0 0 20 20"><path d="M3 5h14v10H3z M3 5l7 6 7-6" fill="none" stroke="#fff" stroke-width="2"/></svg>
      </div>
      <div class="icon-badge">
        <svg viewBox="0 0 20 20"><circle cx="10" cy="10" r="7" fill="none" stroke="#fff" stroke-width="2"/><path d="M3 10h14M10 3c3 3 3 11 0 14M10 3c-3 3-3 11 0 14" fill="none" stroke="#fff" stroke-width="1.5"/></svg>
      </div>
    </div>
    <ul class="contact-list">
      <li class="contact-phone">555-204-7719</li>
      <li class="contact-email">elena@vantiqo.com</li>
      <li class="contact-web">www.vantiqo.com</li>
    </ul>
  </section>

  <section class="card card-back">
    <div class="brand-dot" aria-hidden="true"></div>
    <p class="brand-name">Vantiqo</p>
  </section>
</body>
</html>
```